Tech business card design

We need an amazing business card design for our new business 'Pexla' a marketing tech startup based in Sydney, Australia. We provide an online marketplace for businesses to search and buy advertising media, connect with service providers and learn more about marketing. We wish to communicate 'cool tech', reliability and professionalism and design based around our logo.

Target Market(s)

Business Owners

Contact Information for Business Card

Name
Position
Email Address
Website
Phone Number

Font styles to use
Other font styles liked:
• Avenir & Avenir Next

Colors

Designer to choose colors to be used in the design.

```html
<!DOCTYPE html>
<html lang="en">
<head>
<meta charset="utf-8">
<title>Pexla Business Card</title>
<link href="https://fonts.googleapis.com/css2?family=Nunito+Sans:wght@400;700;900&display=swap" rel="stylesheet">
<style>
  :root {
    --backdrop: #1f1f21;
    --card-glow: #3b66b2;
    --card-mid: #2f4a95;
    --card-edge: #272866;
    --ink-white: #ffffff;
    --ink-grey: #9aa1b8;
    --ink-soft: #c9cde0;
  }
  * { margin: 0; padding: 0; box-sizing: border-box; }
  html, body {
    width: 1200px; height: 945px; overflow: hidden;
    background: var(--backdrop);
    font-family: "Nunito Sans", Arial, sans-serif;
  }
  .canvas { position: relative; width: 1200px; height: 945px; }
  .card {
    position: absolute; width: 620px; height: 354px;
    background: radial-gradient(ellipse at 60% 45%, var(--card-glow) 0%, var(--card-mid) 40%, var(--card-edge) 100%);
    box-shadow: 0 18px 40px rgba(0,0,0,0.55);
    overflow: hidden;
  }
  .card--details { left: 140px; top: 90px; }
  .card--front { left: 440px; top: 500px; }

  .wordmark {
    position: absolute; color: var(--ink-white);
    font-weight: 900; letter-spacing: -2px; line-height: 1;
  }
  .card--details .wordmark { left: 40px; bottom: 48px; font-size: 96px; }
  .card--front .wordmark { left: 0; right: 0; top: 86px; text-align: center; font-size: 130px; }

  .contact { position: absolute; left: 360px; top: 70px; color: var(--ink-white); }
  .contact__name { color: var(--ink-grey); font-weight: 900; font-size: 20px; letter-spacing: 0.5px; }
  .contact__role { color: var(--ink-grey); font-weight: 700; font-size: 15px; margin-bottom: 18px; }
  .contact__address { font-size: 15px; line-height: 1.3; margin-bottom: 14px; }
  .contact__line { display: flex; align-items: center; gap: 10px; font-size: 15px; line-height: 1.45; }
  .contact__line svg { width: 14px; height: 14px; fill: none; stroke: var(--ink-grey); stroke-width: 1.6; }

  .front__web {
    position: absolute; left: 0; right: 0; bottom: 40px; text-align: center;
    color: var(--ink-soft); font-size: 18px; letter-spacing: 5px;
  }
</style>
</head>
<body>
<main class="canvas">
  <section class="card card--details">
    <div class="wordmark">pexla</div>
    <div class="contact">
      <p class="contact__name">JOHN SMITH</p>
      <p class="contact__role">Position</p>
      <p class="contact__address">Street Name, City Name<br>Zipcode:012345</p>
      <p class="contact__line">
        <svg viewBox="0 0 16 16"><path d="M4 2l2.5 3-1.5 1.5c1 2 2.5 3.5 4.5 4.5L11 9.5l3 2.5-1.5 2C7 14 2 9 2 3.5z"/></svg>
        012-345-6789
      </p>
      <p class="contact__line">
        <svg viewBox="0 0 16 16"><rect x="1.5" y="3.5" width="13" height="9"/><path d="M1.5 3.5L8 9l6.5-5.5"/></svg>
        info@pexla.com
      </p>
      <p class="contact__line">
        <svg viewBox="0 0 16 16"><circle cx="8" cy="8" r="6.5"/><ellipse cx="8" cy="8" rx="3" ry="6.5"/><path d="M1.5 8h13"/></svg>
        www.pexla.com
      </p>
    </div>
  </section>

  <section class="card card--front">
    <div class="wordmark">pexla</div>
    <p class="front__web">www.pexla.com</p>
  </section>
</main>
</body>
</html>
```